New Business Card Design Project

Use the flyer uploaded and website www.brightoakbuilders.com for inspiration.
List Our Services on Backside of business cards
Marcus Delling
Harborline Builders Inc.
Licensed General Contractors
858-471-6093

Contact Information for Business Card

Use the flyer uploaded and website www.brightoakbuilders.com for inspiration. List Our Services on Backside of business cards Marcus Delling Harborline Builders Inc. Licensed General Contractors 858-471-6093

```html
<!DOCTYPE html>
<html lang="en">
<head>
<meta charset="utf-8">
<title>Harborline Builders – Business Card</title>
<link rel="stylesheet" href="https://fonts.googleapis.com/css2?family=Roboto:wght@300;400;500&family=Roboto+Condensed:ital,wght@0,700;1,700&display=swap">
<style>
  :root{
    --page:#2b2d31;
    --card:#1e1d21;
    --ink:#f2f2f2;
    --muted:#cfcfd2;
    --red:#e41e26;
    --blue:#4a7fd6;
    --white-band:#e6e6e6;
    --rule:#d9d9d9;
  }
  *{box-sizing:border-box;margin:0;padding:0}
  html,body{width:1200px;height:780px;overflow:hidden;background:var(--page)}
  body{font-family:"Roboto",Arial,sans-serif;color:var(--ink);position:relative}

  .card{
    position:absolute;top:235px;width:540px;height:310px;
    background:var(--card);border-radius:16px;overflow:hidden;
  }
  .card--front{left:40px}
  .card--back{left:620px}

  .brand-name{
    font-family:"Roboto",Arial,sans-serif;font-weight:300;
    text-transform:uppercase;letter-spacing:3px;color:var(--ink);
  }

  /* front */
  .front-brand{position:absolute;left:28px;top:110px;width:200px;text-align:center;font-size:19px;line-height:1.35}
  .front-divider{position:absolute;left:250px;top:38px;width:1px;height:200px;background:var(--rule)}
  .front-bands{position:absolute;left:0;bottom:0;width:540px;height:60px}
  .contact{position:absolute;left:278px;top:62px;right:20px}
  .contact__name{
    font-family:"Roboto Condensed",Arial,sans-serif;font-weight:700;
    font-size:32px;color:var(--red);text-transform:uppercase;line-height:1.05;
  }
  .contact__title,.contact__company{font-size:15px;font-weight:400;margin-top:5px;color:var(--ink)}
  .contact__list{list-style:none;margin-top:16px}
  .contact__item{display:flex;align-items:center;gap:9px;font-size:14.5px;margin-bottom:6px}
  .contact__icon{width:14px;height:14px;flex:none}

  /* back */
  .back-brand{position:absolute;top:52px;left:0;right:0;text-align:center;font-size:24px}
  .back-guarantee{
    position:absolute;top:120px;left:0;right:0;text-align:center;
    font-family:"Roboto Condensed",Arial,sans-serif;font-weight:700;font-style:italic;
    font-size:17px;color:var(--red);letter-spacing:.3px;
  }
  .back-heading{
    position:absolute;top:144px;left:0;right:0;text-align:center;
    font-family:"Roboto Condensed",Arial,sans-serif;font-weight:700;font-style:italic;
    font-size:15px;color:var(--blue);
  }
  .services{position:absolute;top:178px;left:18px;right:18px;text-align:center}
  .services__row{display:flex;justify-content:center;flex-wrap:wrap;gap:4px 10px;margin-bottom:7px}
  .service{display:flex;align-items:center;gap:4px;font-size:12.5px;color:var(--ink)}
  .service__tick{width:11px;height:11px;flex:none}
</style>
</head>
<body>

<section class="card card--front" aria-label="Business card front">
  <div class="front-brand brand-name">Harborline<br>Builders</div>
  <div class="front-divider"></div>

  <div class="contact">
    <h1 class="contact__name">Marcus Delling</h1>
    <p class="contact__title">Licensed General Contractors</p>
    <p class="contact__company">Harborline Builders Inc.</p>
    <ul class="contact__list">
      <li class="contact__item">
        <svg class="contact__icon" viewBox="0 0 24 24"><path fill="var(--red)" d="M6.6 10.8a15.1 15.1 0 0 0 6.6 6.6l2.2-2.2a1 1 0 0 1 1-.25 11.4 11.4 0 0 0 3.6.57 1 1 0 0 1 1 1V20a1 1 0 0 1-1 1A17 17 0 0 1 3 4a1 1 0 0 1 1-1h3.5a1 1 0 0 1 1 1c0 1.25.2 2.45.57 3.57a1 1 0 0 1-.25 1z"/></svg>
        <span>858-471-6093</span>
      </li>
      <li class="contact__item">
        <svg class="contact__icon" viewBox="0 0 24 24"><rect x="2" y="5" width="20" height="14" rx="2" fill="var(--red)"/><path d="M3 6l9 7 9-7" fill="none" stroke="var(--card)" stroke-width="2"/></svg>
        <span>info@brightoakbuilders.com</span>
      </li>
      <li class="contact__item">
        <svg class="contact__icon" viewBox="0 0 24 24"><circle cx="12" cy="12" r="10" fill="var(--red)"/><g fill="none" stroke="var(--card)" stroke-width="1.5"><ellipse cx="12" cy="12" rx="4" ry="10"/><path d="M2 12h20M4 7h16M4 17h16"/></g></svg>
        <span>www.brightoakbuilders.com</span>
      </li>
    </ul>
  </div>

  <svg class="front-bands" viewBox="0 0 540 60" aria-hidden="true">
    <polygon points="0,8 238,8 252,60 0,60" fill="var(--red)"/>
    <polygon points="262,26 540,26 540,60 272,60" fill="var(--white-band)"/>
  </svg>
</section>

<section class="card card--back" aria-label="Business card back">
  <div class="back-brand brand-name">Harborline Builders</div>
  <p class="back-guarantee">OUR SERVICES ARE 100% GUARANTEED</p>
  <p class="back-heading">SPECIALIZING IN:</p>

  <div class="services">
    <div class="services__row">
      <span class="service"><svg class="service__tick" viewBox="0 0 12 12"><path d="M2 6.5l2.6 2.6L10 3" fill="none" stroke="var(--red)" stroke-width="1.8"/></svg>Remodel: Kitchen &amp; Bath</span>
      <span class="service"><svg class="service__tick" viewBox="0 0 12 12"><path d="M2 6.5l2.6 2.6L10 3" fill="none" stroke="var(--red)" stroke-width="1.8"/></svg>Painting: Interior &amp; Exterior</span>
      <span class="service"><svg class="service__tick" viewBox="0 0 12 12"><path d="M2 6.5l2.6 2.6L10 3" fill="none" stroke="var(--red)" stroke-width="1.8"/></svg>Flooring: Carpet, Vinyl, Wood</span>
    </div>
    <div class="services__row">
      <span class="service"><svg class="service__tick" viewBox="0 0 12 12"><path d="M2 6.5l2.6 2.6L10 3" fill="none" stroke="var(--red)" stroke-width="1.8"/></svg>Window &amp; Door Replacement</span>
      <span class="service"><svg class="service__tick" viewBox="0 0 12 12"><path d="M2 6.5l2.6 2.6L10 3" fill="none" stroke="var(--red)" stroke-width="1.8"/></svg>Plumbing: Repairs &amp; Upgrades</span>
      <span class="service"><svg class="service__tick" viewBox="0 0 12 12"><path d="M2 6.5l2.6 2.6L10 3" fill="none" stroke="var(--red)" stroke-width="1.8"/></svg>Energy-Efficient Upgrades</span>
    </div>
    <div class="services__row">
      <span class="service"><svg class="service__tick" viewBox="0 0 12 12"><path d="M2 6.5l2.6 2.6L10 3" fill="none" stroke="var(--red)" stroke-width="1.8"/></svg>Deck &amp; Patio Construction</span>
      <span class="service"><svg class="service__tick" viewBox="0 0 12 12"><path d="M2 6.5l2.6 2.6L10 3" fill="none" stroke="var(--red)" stroke-width="1.8"/></svg>Water &amp; Mold Damage</span>
      <span class="service"><svg class="service__tick" viewBox="0 0 12 12"><path d="M2 6.5l2.6 2.6L10 3" fill="none" stroke="var(--red)" stroke-width="1.8"/></svg>Garage Renovation</span>
    </div>
  </div>
</section>

</body>
</html>
```